New Business Card for Web Design/Internet Marketing Company

Looking for a great looking new business card. We are a 10 year old web design, internet marketing and website management company that works mostly with small businesses.

Our new card needs to better match the colors and style of our website, be bold, extremely usable and slightly edgy.

Target Market(s)

Small/Medium businesses that have websites

Industry/Entity Type

Internet

Requirements
Must have
• Front and back design, full color, rounded corners please

Must use the colors/style of our website (JPG provided)

INFO FOR CARDS (as readable as possible please)
Mark Lenner
President/CEO
mark@trelvanmedia.example
Phone: 520-381-7459
Toll Free: 866-381-7459
Address: 4315 W. Calloway Ave. Ste. 140, Tucson, AZ 85792

THINGS I WANT TO PROMOTE (if there is room):
1. Our Website - www.trelvanmedia.example

2. Social Media
Twitter: @trelvanmedia
Facebook: www.facebook.com/trelvanmedia

3. Our Services
Web Design
Internet Marketing
Website Management

```html
<!DOCTYPE html>
<html lang="en">
<head>
<meta charset="utf-8">
<title>Trelvan Media – Business Card</title>
<link rel="stylesheet" href="https://fonts.googleapis.com/css2?family=Cabin:ital,wght@0,400;0,500;0,600;0,700;1,500&display=swap">
<style>
  :root {
    --canvas-bg: #ecebe8;
    --card-white: #ffffff;
    --brand-orange: #f08a2a;
    --brand-blue: #0a8fc7;
    --text-dark: #2b2b2b;
    --tagline-grey: #7d7d7d;
    --tagline-on-dark: #8d97ad;
    --band-deep: #1b4fa8;
    --band-light: #14a6e0;
    --back-center: #0a55a8;
    --back-edge: #1c1d6b;
    --service-white: #f2f4fb;
  }
  * { box-sizing: border-box; margin: 0; padding: 0; }
  html, body { width: 1200px; height: 900px; overflow: hidden; }
  body {
    background: var(--canvas-bg);
    font-family: "Cabin", sans-serif;
    position: relative;
  }
  .card {
    position: absolute;
    left: 313px;
    width: 541px;
    height: 330px;
    border-radius: 18px;
    overflow: hidden;
    box-shadow: 0 6px 14px rgba(0,0,0,0.18);
  }

  /* Front */
  .card-front { top: 90px; background: var(--card-white); }
  .front-brand {
    position: absolute; left: 44px; top: 36px;
    display: flex; align-items: center; gap: 12px;
  }
  .brand-dot {
    width: 24px; height: 24px; border-radius: 50%;
    background: var(--brand-orange);
  }
  .brand-name {
    font-size: 44px; font-weight: 700; color: var(--brand-blue);
    letter-spacing: -0.5px; line-height: 1;
  }
  .front-tagline {
    position: absolute; right: 100px; top: 84px;
    font-size: 16px; color: var(--tagline-grey);
  }
  .contact { position: absolute; left: 44px; top: 130px; color: var(--text-dark); }
  .contact-name { font-size: 17px; font-weight: 600; color: var(--brand-orange); line-height: 22px; }
  .contact-title { font-size: 15px; line-height: 20px; margin-bottom: 10px; }
  .contact-line { font-size: 15px; line-height: 19.5px; }
  .contact-line .label { color: var(--brand-orange); font-weight: 600; }
  .web-band {
    position: absolute; left: 0; right: 0; bottom: 0; height: 44px;
    background: linear-gradient(90deg, var(--band-deep) 0%, var(--band-light) 50%, var(--band-deep) 100%);
    display: flex; align-items: center; justify-content: center;
    color: #fff; font-style: italic; font-weight: 500; font-size: 19px; letter-spacing: 0.3px;
  }

  /* Back */
  .card-back {
    top: 458px;
    background: radial-gradient(ellipse at 50% 45%, var(--back-center) 0%, #0b3f93 55%, var(--back-edge) 100%);
  }
  .back-brand {
    position: absolute; left: 0; right: 0; top: 110px;
    display: flex; align-items: center; justify-content: center; gap: 14px;
  }
  .back-brand .brand-dot { width: 32px; height: 32px; }
  .back-brand .brand-name { font-size: 58px; }
  .back-tagline {
    position: absolute; right: 130px; top: 186px;
    font-size: 20px; color: var(--tagline-on-dark);
  }
  .services {
    position: absolute; left: 0; right: 0; top: 280px;
    display: flex; justify-content: center; align-items: center; gap: 12px;
    color: var(--service-white); font-size: 18px; letter-spacing: 0.4px;
  }
  .service-sep {
    width: 7px; height: 7px; border-radius: 50%;
    background: var(--brand-orange); margin-top: 12px;
  }
</style>
</head>
<body>
  <section class="card card-front">
    <div class="front-brand">
      <span class="brand-dot"></span>
      <span class="brand-name">Trelvan Media</span>
    </div>
    <div class="front-tagline">Sites that Deliver</div>

    <div class="contact">
      <div class="contact-name">Mark Lenner</div>
      <div class="contact-title">President/CEO</div>
      <div class="contact-line">mark@trelvanmedia.example</div>
      <div class="contact-line"><span class="label">P:</span> 520-381-7459</div>
      <div class="contact-line"><span class="label">Toll Free:</span> 866-381-7459</div>
      <div class="contact-line"><span class="label">A:</span> 4315 W. Calloway Ave. Ste. 140,</div>
      <div class="contact-line">Tucson, AZ 85792</div>
    </div>

    <div class="web-band">www.trelvanmedia.example</div>
  </section>

  <section class="card card-back">
    <div class="back-brand">
      <span class="brand-dot"></span>
      <span class="brand-name">Trelvan Media</span>
    </div>
    <div class="back-tagline">Sites that Deliver</div>
    <div class="services">
      <span>Web Design</span>
      <span class="service-sep"></span>
      <span>Internet Marketing</span>
      <span class="service-sep"></span>
      <span>Website Management</span>
    </div>
  </section>
</body>
</html>
```